Heavy Duty Repairs Poster

Good afternoon - I'm looking for a poster , design to set up around different areas. The Poster must consist of the following
- Heavy duty repairs
- Pictures of Semi trucks , heavy construction equipment , trailers
- Agriculture
- All north American equipment ( see attached pictures)
- Brief Descriptions in bullet point forms
CVIPS
WELDING
AIR CONDITIONING
ENGINE REBUILDS
DIAGONSTICS
FLEET MANAGMENT
TIRE REPAIR AND SALES
ELECTRICAL , HYDRALIC , POWER TRAIN SERVICE AND REPAIRS
PART SALES
FLEET MAINTINACE
DELTEING AND TUNING
AFTER MARKET INSTALLS OUTFITTING
ONSITE & OFFSITE REPAIRS
FULL RECERTIFACTION OVERHAULING
Warranty Approved

Target Market(s)

Heavy Duty Truck , Equipment , Agriculture Owners

Industry/Entity Type

Heavy Duty Repairs

Colors
EB3D1F
EC4F4E
F09395
F8D3D4
FCEDEE

Requirements
Must have
• Pictures of : Semi trucks and trailer , Construction heavy equipment , agriculture equipment
Nice to have
• Flashy and stands out

```html
<!DOCTYPE html>
<html lang="en">
<head>
<meta charset="utf-8">
<title>Heavy Duty Repairs Poster</title>
<link href="https://fonts.googleapis.com/css2?family=Oswald:wght@500;700&display=swap" rel="stylesheet">
<style>
  :root {
    --red: #EB3D1F;
    --red-soft: #EC4F4E;
    --pink: #F09395;
    --blush: #F8D3D4;
    --mist: #FCEDEE;
    --ink: #0a0a0a;
    --white: #ffffff;
    --stage: #e6ebe8;
  }
  * { margin: 0; padding: 0; box-sizing: border-box; }
  html, body { width: 1200px; height: 742px; overflow: hidden; background: var(--stage); }
  body { font-family: "Oswald", sans-serif; }

  .poster {
    position: absolute; left: 357px; top: 21px;
    width: 486px; height: 700px;
    background: var(--ink); overflow: hidden;
    box-shadow: 0 6px 18px rgba(0,0,0,.35);
  }
  .brand-name {
    position: absolute; top: 80px; width: 100%; text-align: center;
    color: var(--white); font-weight: 500; font-size: 28px; line-height: 36px; letter-spacing: .5px;
  }
  .brand-name .dot {
    display: inline-block; width: 13px; height: 13px; border-radius: 50%;
    background: var(--red); margin-right: 10px; vertical-align: 3px;
  }
  .city {
    position: absolute; top: 120px; width: 100%; text-align: center;
    color: var(--red); font-weight: 500; font-size: 23px; line-height: 30px; letter-spacing: 2px;
  }
  .headline {
    position: absolute; top: 152px; width: 100%; text-align: center;
    color: var(--white); font-weight: 700; font-size: 49px; line-height: 54px;
    transform: scaleX(.94); z-index: 2;
  }
  .hex-field { position: absolute; left: 0; top: 0; width: 486px; height: 700px; }

  .wrench-tag {
    position: absolute; left: 198px; top: 398px;
    color: var(--red); font-weight: 700; font-size: 19px; line-height: .95;
    transform: rotate(-18deg);
  }
  .sector {
    position: absolute; width: 130px; text-align: center;
    color: var(--pink); font-weight: 700; font-size: 14px; line-height: 18px;
  }
  .sector.equipment { left: 36px; top: 492px; }
  .sector.industries { left: 322px; top: 492px; }

  .services {
    position: absolute; top: 568px; left: 6px; right: 6px; text-align: center;
    color: var(--white); font-weight: 500; font-size: 9.4px; line-height: 13.5px;
    letter-spacing: -.1px;
  }
  .services .sep { color: var(--red); padding: 0 2px; }
  .warranty {
    position: absolute; top: 612px; left: 50%; transform: translateX(-50%);
    background: var(--red); color: var(--white); border: 1px solid var(--white);
    font-size: 8px; font-weight: 700; letter-spacing: 2.5px; padding: 0 5px; line-height: 12px;
    white-space: nowrap;
  }
  .phone {
    position: absolute; top: 632px; width: 100%; text-align: center;
    color: var(--red); font-weight: 700; font-size: 56px; line-height: 60px; letter-spacing: 1px;
  }
</style>
</head>
<body>
  <main class="poster">
    <svg class="hex-field" viewBox="0 0 486 700">
      <defs>
        <linearGradient id="frameFill" x1="0" y1="0" x2="0" y2="1">
          <stop offset="0" stop-color="#1c1c1c"/><stop offset="1" stop-color="#050505"/>
        </linearGradient>
        <linearGradient id="truckTone" x1="0" y1="0" x2="0" y2="1">
          <stop offset="0" stop-color="#3d6fb8"/><stop offset=".5" stop-color="#c9ccd2"/><stop offset="1" stop-color="#3b3b44"/>
        </linearGradient>
        <linearGradient id="constructionTone" x1="0" y1="0" x2="0" y2="1">
          <stop offset="0" stop-color="#4a4a44"/><stop offset=".6" stop-color="#c98a2a"/><stop offset="1" stop-color="#3a3228"/>
        </linearGradient>
        <linearGradient id="farmTone" x1="0" y1="0" x2="0" y2="1">
          <stop offset="0" stop-color="#5b6b7c"/><stop offset=".55" stop-color="#3d8c3a"/><stop offset="1" stop-color="#2f4a22"/>
        </linearGradient>
        <linearGradient id="toolTone" x1="0" y1="0" x2="0" y2="1">
          <stop offset="0" stop-color="#6e6454"/><stop offset="1" stop-color="#2e2a24"/>
        </linearGradient>
      </defs>

      <g class="frame-hex" fill="url(#frameFill)" stroke="var(--red)" stroke-width="1.5">
        <polygon points="18,242 58,200 140,200 180,242 140,284 58,284"/>
        <polygon points="304,242 344,200 426,200 466,242 426,284 344,284"/>
        <polygon points="20,515 60,455 140,455 180,515 140,575 60,575"/>
        <polygon points="306,515 346,455 426,455 466,515 426,575 346,575"/>
      </g>

      <rect role="img" aria-label="Photo of a large steel wrench" x="168" y="382" width="152" height="178" rx="10" fill="url(#toolTone)"/>

      <g role="img" aria-label="Photo of construction equipment: excavators and loaders">
        <polygon points="157,290 200,215 286,215 329,290 286,365 200,365" fill="url(#constructionTone)" stroke="#fff" stroke-width="2"/>
      </g>
      <g role="img" aria-label="Photo of semi trucks and trailers on the highway">
        <polygon points="16,372 59,297 145,297 188,372 145,447 59,447" fill="url(#truckTone)" stroke="#fff" stroke-width="2"/>
      </g>
      <g role="img" aria-label="Photo of agricultural equipment: tractors and combines">
        <polygon points="298,372 341,297 427,297 470,372 427,447 341,447" fill="url(#farmTone)" stroke="#fff" stroke-width="2"/>
      </g>
    </svg>

    <div class="brand-name"><span class="dot"></span>Ridgeway Mechanical Services</div>
    <div class="city">Pine Hollow, Alberta</div>
    <h1 class="headline">HEAVY DUTY REPAIRS</h1>

    <div class="wrench-tag">HEAVY<br>DUTY<br>REPAIRS</div>

    <div class="sector equipment">HEAVY DUTY<br>NORTH AMERICAN<br>EQUIPMENT</div>
    <div class="sector industries">CONSTRUCTION<br>TRANSPORTATION<br>AGRICULTURE</div>

    <p class="services">
      CVIPS <span class="sep">•</span> WELDING <span class="sep">•</span> AIR CONDITIONING <span class="sep">•</span> ENGINE REBUILDS <span class="sep">•</span> DIAGONSTICS <span class="sep">•</span> FLEET MANAGMENT <span class="sep">•</span> TIRE REPAIR AND SALES<br>
      ELECTRICAL , HYDRALIC , POWER TRAIN SERVICE AND REPAIRS <span class="sep">•</span> PART SALES <span class="sep">•</span> FLEET MAINTINACE <span class="sep">•</span> DELTEING AND TUNING<br>
      AFTER MARKET INSTALLS OUTFITTING <span class="sep">•</span> ONSITE &amp; OFFSITE REPAIRS <span class="sep">•</span> FULL RECERTIFACTION OVERHAULING
    </p>
    <div class="warranty">WARRANTY APPROVED</div>
    <div class="phone">555-014-2294</div>
  </main>
</body>
</html>
```